Sole Relationship Graphic of Chapter Organization for Book

This design shows relationships between variables associated with footwear and footprints. It will be used as a graphic in a book. The four elements of the graphic are (1) Variables, (2) Book Chapter Numbers (which correspond to the relationship(s) between at least two variables, (3) Relationship Arrows, and (4) Influence Arrows (because the influencers affect the variables differently than relationships between the variables). These names simply relate to the attempts I have made (and attached) at creating a graphic. In the attached diagrams, the circles with numbers are placeholders for the book chapter numbers, which may be changed so it will be good if I can change those after the graphic is completed. Chapter 1 will be the introduction.
The intent of of outsourcing this project is not necessarily sticking to the formats I have attached, but to allow your creativity to produce a useful graphic that can visually make the most sense of the relationships between the variables as chapters to readers of the book.

Target Market(s)

Search and Rescue Trackers

Requirements
Must have
• Information listed in project description, and drafted in attached diagrams
Nice to have
• Can include outlines of barefoot and outsoles. While Chapters 1 (Intro), 2 (Missing Persons' Footwear), 10 (Case Studies) and 11 (Summary) are set, the others aren't. The end game of this book is to use the rest of the variables to arrive at the end game, which is measurements for barefoot track length or outsole track length...so those two variables can be highlighted in some way to emphasize their importance.

```html
<!DOCTYPE html>
<html lang="en">
<head>
<meta charset="utf-8">
<title>Footwear and Footprint Variables – Chapter Map</title>
<link rel="stylesheet" href="https://fonts.googleapis.com/css2?family=Barlow+Condensed:wght@600;700&family=Barlow+Semi+Condensed:wght@500;600&display=swap">
<style>
  :root {
    --green: #218c6f;
    --slate: #4b5451;
    --red: #b8202e;
    --paper: #ffffff;
    --shoe-fill: #d6d6d6;
    --foot-fill: #c2272d;
  }
  html, body {
    margin: 0;
    padding: 0;
    width: 1200px;
    height: 675px;
    overflow: hidden;
    background: var(--paper);
  }
  .diagram { display: block; width: 1200px; height: 675px; }
  .title { font-family: "Barlow Condensed", sans-serif; font-weight: 700; font-size: 33px; fill: var(--red); }
  .label { font-family: "Barlow Semi Condensed", sans-serif; font-weight: 600; font-size: 19px; fill: var(--slate); }
  .band-label { font-family: "Barlow Semi Condensed", sans-serif; font-weight: 600; font-size: 19px; fill: var(--paper); }
  .variation-label { font-family: "Barlow Semi Condensed", sans-serif; font-weight: 600; font-size: 21px; fill: var(--paper); }
  .legend-title { font-family: "Barlow Condensed", sans-serif; font-weight: 700; font-size: 25px; fill: var(--slate); }
  .chapter-num { font-family: "Barlow Semi Condensed", sans-serif; font-weight: 600; font-size: 18px; fill: var(--green); }
  .chapter-ring { fill: var(--paper); stroke: var(--green); stroke-width: 2.5; }
  .relation { fill: none; stroke: var(--slate); stroke-width: 5; }
  .influence { fill: none; stroke: var(--green); stroke-width: 5; }
  .frame { fill: var(--paper); stroke: var(--green); stroke-width: 3; }
  .band { fill: var(--green); }
  .variation-box { fill: var(--slate); }
  .shoe-art { fill: var(--shoe-fill); }
  .foot-art { fill: var(--foot-fill); }
  .track-badge { fill: var(--slate); }
  .legend-box { fill: none; stroke: var(--slate); stroke-width: 2; }
</style>
</head>
<body>
<svg class="diagram" viewBox="0 0 1280 720" xmlns="http://www.w3.org/2000/svg">
  <defs>
    <marker id="head-slate" viewBox="0 0 10 10" refX="8" refY="5" markerWidth="3.2" markerHeight="3.2" orient="auto-start-reverse">
      <path d="M0,0 L10,5 L0,10 z" fill="#4b5451"/>
    </marker>
    <marker id="head-green" viewBox="0 0 10 10" refX="8" refY="5" markerWidth="3.2" markerHeight="3.2" orient="auto-start-reverse">
      <path d="M0,0 L10,5 L0,10 z" fill="#218c6f"/>
    </marker>
  </defs>

  <!-- Title -->
  <text class="title" x="645" y="90" text-anchor="middle">MISSING PERSONS’</text>
  <text class="title" x="645" y="123" text-anchor="middle">FOOTWEAR</text>

  <!-- Relationship lines -->
  <path class="relation" d="M512,88 H393 V166" marker-end="url(#head-slate)"/>
  <path class="relation" d="M780,88 H900 V166" marker-end="url(#head-slate)"/>
  <path class="relation" d="M483,217 H809" marker-start="url(#head-slate)" marker-end="url(#head-slate)"/>
  <path class="relation" d="M574,266 H484" marker-end="url(#head-slate)"/>
  <path class="relation" d="M718,266 H808" marker-end="url(#head-slate)"/>
  <path class="relation" d="M646,318 V403" marker-end="url(#head-slate)"/>
  <path class="relation" d="M195,255 H303" marker-end="url(#head-slate)"/>

  <!-- Influence lines -->
  <path class="influence" d="M559,427 H418 V340" marker-end="url(#head-green)"/>
  <path class="influence" d="M646,444 V494" marker-end="url(#head-green)"/>
  <path class="influence" d="M372,340 V545 H566" marker-start="url(#head-green)" marker-end="url(#head-green)"/>
  <path class="influence" d="M505,591 H566" marker-end="url(#head-green)"/>
  <path class="influence" d="M987,254 H1089" marker-end="url(#head-green)"/>
  <path class="influence" d="M724,562 H882" marker-end="url(#head-green)"/>

  <!-- Insole Length -->
  <g class="variable">
    <rect class="frame" x="308" y="172" width="171" height="162"/>
    <rect class="shoe-art" x="326" y="190" width="140" height="88" rx="18" role="img" aria-label="Shoe illustration with insole outline highlighted"/>
    <rect class="band" x="307" y="298" width="173" height="37"/>
    <text class="band-label" x="393" y="323" text-anchor="middle">Insole Length</text>
  </g>

  <!-- Outsole Length -->
  <g class="variable">
    <rect class="frame" x="814" y="172" width="171" height="162"/>
    <rect class="shoe-art" x="832" y="190" width="140" height="88" rx="18" role="img" aria-label="Shoe illustration with outsole outline highlighted"/>
    <rect class="band" x="813" y="298" width="173" height="37"/>
    <text class="band-label" x="899" y="323" text-anchor="middle">Outsole Length</text>
  </g>

  <!-- Individual Variation -->
  <rect class="variation-box" x="574" y="238" width="144" height="80" rx="10"/>
  <text class="variation-label" x="646" y="273" text-anchor="middle">Individual</text>
  <text class="variation-label" x="646" y="297" text-anchor="middle">Variation</text>

  <!-- Nominal Size -->
  <rect class="band" x="559" y="407" width="174" height="37"/>
  <text class="band-label" x="646" y="432" text-anchor="middle">Nominal Size</text>

  <!-- Barefoot -->
  <g class="variable">
    <rect class="frame" x="572" y="499" width="149" height="125"/>
    <rect class="foot-art" x="598" y="512" width="96" height="64" rx="14" role="img" aria-label="Bare foot illustration"/>
    <rect class="band" x="571" y="588" width="151" height="37"/>
    <text class="band-label" x="646" y="613" text-anchor="middle">Barefoot</text>
  </g>

  <!-- Influencer labels -->
  <text class="label" x="161" y="250" text-anchor="middle">Hook</text>
  <text class="label" x="161" y="271" text-anchor="middle">Area</text>
  <text class="label" x="468" y="598" text-anchor="middle">Height</text>

  <!-- Outcome tracks -->
  <circle class="track-badge" cx="1134" cy="251" r="43" role="img" aria-label="Shoe track prints icon"/>
  <text class="label" x="1134" y="320" text-anchor="middle">Shoe Track</text>
  <text class="label" x="1134" y="340" text-anchor="middle">Length</text>

  <circle class="track-badge" cx="931" cy="562" r="43" role="img" aria-label="Barefoot track prints icon"/>
  <text class="label" x="931" y="630" text-anchor="middle">Barefoot Track</text>
  <text class="label" x="931" y="650" text-anchor="middle">Length</text>

  <!-- Chapter markers -->
  <g class="chapter"><circle class="chapter-ring" cx="438" cy="120" r="13"/><text class="chapter-num" x="438" y="126" text-anchor="middle">2</text></g>
  <g class="chapter"><circle class="chapter-ring" cx="822" cy="120" r="13"/><text class="chapter-num" x="822" y="126" text-anchor="middle">2</text></g>
  <g class="chapter"><circle class="chapter-ring" cx="646" cy="193" r="13"/><text class="chapter-num" x="646" y="199" text-anchor="middle">5</text></g>
  <g class="chapter"><circle class="chapter-ring" cx="532" cy="291" r="13"/><text class="chapter-num" x="532" y="297" text-anchor="middle">7</text></g>
  <g class="chapter"><circle class="chapter-ring" cx="759" cy="291" r="13"/><text class="chapter-num" x="759" y="297" text-anchor="middle">7</text></g>
  <g class="chapter"><circle class="chapter-ring" cx="619" cy="353" r="13"/><text class="chapter-num" x="619" y="359" text-anchor="middle">5</text></g>
  <g class="chapter"><circle class="chapter-ring" cx="238" cy="278" r="13"/><text class="chapter-num" x="238" y="284" text-anchor="middle">3</text></g>
  <g class="chapter"><circle class="chapter-ring" cx="476" cy="449" r="13"/><text class="chapter-num" x="476" y="455" text-anchor="middle">9</text></g>
  <g class="chapter"><circle class="chapter-ring" cx="672" cy="467" r="13"/><text class="chapter-num" x="672" y="473" text-anchor="middle">4</text></g>
  <g class="chapter"><circle class="chapter-ring" cx="343" cy="491" r="13"/><text class="chapter-num" x="343" y="497" text-anchor="middle">9</text></g>
  <g class="chapter"><circle class="chapter-ring" cx="532" cy="617" r="13"/><text class="chapter-num" x="532" y="623" text-anchor="middle">8</text></g>
  <g class="chapter"><circle class="chapter-ring" cx="1034" cy="231" r="13"/><text class="chapter-num" x="1034" y="237" text-anchor="middle">6</text></g>
  <g class="chapter"><circle class="chapter-ring" cx="805" cy="542" r="13"/><text class="chapter-num" x="805" y="548" text-anchor="middle">9</text></g>

  <!-- Legend -->
  <text class="legend-title" x="49" y="549">LEGEND</text>
  <rect class="legend-box" x="47" y="566" width="264" height="105"/>
  <g class="chapter"><circle class="chapter-ring" cx="136" cy="591" r="13"/><text class="chapter-num" x="136" y="597" text-anchor="middle">1</text></g>
  <text class="label" x="170" y="598">Chapter #</text>
  <path class="relation" d="M57,622 H149" marker-end="url(#head-slate)"/>
  <text class="label" x="170" y="629">Relationship to</text>
  <path class="influence" d="M57,651 H149" marker-end="url(#head-green)"/>
  <text class="label" x="170" y="658">Influence on</text>
</svg>
</body>
</html>
```